Newsletter Ad

I am looking for someone to design an advertisement for a mother's club newsletter. 4" wide X by 5" tall (and 2.5" wide X 5" tall if possible).

I'm a psychotherapist, so want the ad to look professional, but modern. I have a logo with my photo attached that can be incorporated into the design. The colors of my website are turquoise and white. I'd like to keep with that theme...so maybe some turquoise blocking to match the logo font color.

I'm uploading a logo as well as an ad draft with the content I'd like listed in the ad.

```html
<!DOCTYPE html>
<html lang="en">
<head>
<meta charset="UTF-8">
<title>Dana Rowe, MA, MFT – Newsletter Ad</title>
<link rel="stylesheet" href="https://fonts.googleapis.com/css2?family=Roboto+Condensed:wght@300;400;700&family=Josefin+Sans:wght@400&display=swap">
<style>
  :root {
    --teal: #4b9f9e;
    --white: #ffffff;
    --photo-dark: #1c1a18;
    --photo-warm: #8a6a52;
  }
  * { margin: 0; padding: 0; box-sizing: border-box; }
  html, body { width: 961px; height: 1200px; overflow: hidden; background: var(--white); }
  .ad {
    position: relative;
    width: 961px;
    height: 1200px;
    overflow: hidden;
    font-family: "Roboto Condensed", "Arial Narrow", sans-serif;
    background: var(--white);
  }
  .hero {
    position: absolute;
    left: 0; top: 0;
    width: 961px; height: 882px;
    background: var(--teal);
    color: var(--white);
  }
  .headline {
    position: absolute;
    left: 0; top: 46px;
    width: 100%;
    text-align: center;
    font-weight: 400;
    font-size: 64px;
    line-height: 80px;
  }
  .services { list-style: none; }
  .service {
    position: absolute;
    left: 55px;
    font-size: 44px;
    line-height: 1;
    padding-bottom: 10px;
    border-bottom: 3px solid var(--white);
  }
  .service--last { border-bottom: none; }
  .contact-card {
    position: absolute;
    left: 474px; top: 298px;
    width: 452px; height: 428px;
    background: var(--white);
    color: var(--teal);
    text-align: center;
  }
  .contact-card__cta {
    margin-top: 38px;
    font-weight: 700;
    font-size: 52px;
    line-height: 60px;
  }
  .contact-card__phone {
    margin-top: 14px;
    font-weight: 700;
    font-size: 62px;
    line-height: 70px;
    letter-spacing: 1px;
  }
  .contact-card__details {
    margin-top: 8px;
    font-style: normal;
    font-size: 37px;
    line-height: 53px;
  }
  .portrait {
    position: absolute;
    left: 21px; top: 899px;
    width: 276px; height: 280px;
    background: linear-gradient(135deg, var(--photo-dark) 0%, var(--photo-warm) 55%, var(--photo-dark) 100%);
  }
  .bio { position: absolute; left: 318px; top: 914px; width: 622px; color: var(--teal); }
  .bio__name {
    font-family: "Josefin Sans", "Gill Sans", sans-serif;
    font-weight: 400;
    font-size: 50px;
    line-height: 66px;
    letter-spacing: 0;
    white-space: nowrap;
  }
  .bio__text {
    margin-top: 18px;
    font-size: 23px;
    line-height: 34px;
    text-align: justify;
  }
  .license {
    position: absolute;
    right: 36px; top: 1146px;
    color: var(--teal);
    font-size: 30px;
  }
</style>
</head>
<body>
  <main class="ad">
    <section class="hero">
      <h1 class="headline">Psychotherapy for Individuals<br>Couples and Families</h1>
      <ul class="services">
        <li class="service" style="top:262px;width:158px;">Anxiety</li>
        <li class="service" style="top:341px;width:186px;">Divorce</li>
        <li class="service" style="top:413px;width:222px;left:53px;">Parenting</li>
        <li class="service" style="top:490px;width:252px;left:53px;">Depression</li>
        <li class="service" style="top:562px;width:269px;">Couples Issues</li>
        <li class="service" style="top:636px;width:309px;left:53px;">Life Transitions</li>
        <li class="service" style="top:712px;width:476px;left:53px;padding-bottom:14px;">Women’s Issues</li>
        <li class="service service--last" style="top:789px;">Attachment &amp; Neuroscience</li>
      </ul>
      <div class="contact-card">
        <p class="contact-card__cta">Call Now</p>
        <p class="contact-card__phone">415 555 0186</p>
        <address class="contact-card__details">
          148 Alder Street<br>
          Cedar Glen, CA 94900<br>
          www.danarowe.com<br>
          dana@danarowe.com
        </address>
      </div>
    </section>

    <div class="portrait" role="img" aria-label="Portrait photograph of the therapist"></div>

    <section class="bio">
      <h2 class="bio__name">DANA ROWE, MA, MFT</h2>
      <p class="bio__text">Dana Rowe is a psychotherapist with a private practice in Cedar Glen, California. With over 15 years of experience, Dana’s areas of expertise include depression, anxiety, trauma, life transitions, parenting, and relationship issues.</p>
    </section>
    <p class="license">License# MFC48213</p>
  </main>
</body>
</html>
```